Looking for a5 flyer for domestic properties in Scotland
One side on Air Source Heat pumps (air to water Heat pump) Instalation + maintenance
Other side Air to Air Heat Pumps also knows as Air Conditioning Heat Pumps. Installation
Design to be Black white with red blue
Harlow- Climawell Services

Need sell the benifts of large energy savings over oil and lpg and lowering carbon footprint

```html
<!DOCTYPE html>
<html lang="en">
<head>
<meta charset="utf-8">
<title>Harlow – Climawell Services flyers</title>
<link rel="stylesheet" href="https://fonts.googleapis.com/css2?family=Oswald:wght@500;600&family=Roboto:wght@400;500;700&family=Roboto+Condensed:wght@700&display=swap">
<style>
:root{
  --red:#ea5426;
  --blue:#2aa3de;
  --ink:#1c1c1c;
  --text:#444;
  --dark:#2d2f32;
  --page:#e9eaec;
  --white:#fff;
}
*{box-sizing:border-box;margin:0;padding:0}
html,body{width:1200px;height:900px;overflow:hidden;background:var(--page)}
body{font-family:"Roboto",Arial,sans-serif;color:var(--text);position:relative}
.flyer{position:absolute;top:54px;width:560px;height:792px;background:var(--white);overflow:hidden;box-shadow:0 4px 18px rgba(0,0,0,.18)}
.flyer--heat{left:30px}
.flyer--air{left:610px}
.abs{position:absolute}
.brand{position:absolute;z-index:2;font-family:"Roboto Condensed",Arial,sans-serif;font-weight:700;color:var(--ink);font-size:60px;line-height:1;letter-spacing:-1px}
.tagline{position:absolute;z-index:2;font-family:"Roboto Condensed",Arial,sans-serif;font-weight:700;font-size:15px;line-height:1.2;color:var(--ink)}
.phone-pill{position:absolute;z-index:2;height:34px;width:196px;background:var(--ink);border-radius:17px;display:flex;align-items:center;color:var(--white);font-weight:700;font-size:20px;letter-spacing:.5px}
.phone-pill .dot{width:34px;height:34px;border-radius:50%;background:var(--red);display:flex;align-items:center;justify-content:center;margin-right:10px;border:3px solid var(--white)}
.pill-note{position:absolute;z-index:2;font-size:10px;line-height:1.25;color:var(--ink);text-align:right}
.photo{position:absolute;overflow:hidden}
.photo--family{left:0;top:170px;width:560px;height:240px;background:linear-gradient(120deg,#d9dcdf 0%,#b9bcbf 40%,#8b8178 70%,#c4c7ca 100%)}
.photo--garden{left:0;top:0;width:560px;height:320px;background:linear-gradient(160deg,#6f8f5c 0%,#b7c2c9 35%,#e4e6e8 55%,#4e6b3a 100%)}
.inset{position:absolute;width:112px;height:112px;border-radius:50%;border:5px solid var(--red);box-shadow:0 0 0 3px var(--white);background:linear-gradient(135deg,#f2f2f2,#9a9ea2)}
.heading{position:absolute;font-family:"Oswald",Arial,sans-serif;font-weight:600;font-size:24px;color:var(--ink);line-height:1.1;text-transform:uppercase;letter-spacing:-.3px;white-space:nowrap}
.rule{position:absolute;height:1px;background:#bbb}
.subhead{position:absolute;font-weight:500;font-size:17px;color:var(--ink);line-height:1.2}
.body-copy{position:absolute;font-size:10.5px;line-height:1.4;text-align:justify;color:var(--text)}
.body-copy p+p{margin-top:8px}
.benefits{position:absolute;list-style:none}
.benefits li{display:flex;align-items:center;font-size:12px;color:var(--text);line-height:1.15}
.benefits svg{flex:none;margin-right:8px}
.benefits--heat li{height:31px}
.benefits--air li{height:32px;font-size:12.5px}
.vline{position:absolute;width:1px;background:#ccc}
.price{position:absolute;font-weight:700;font-size:12.5px;color:var(--ink);line-height:1.3}
.footer{position:absolute;left:0;right:0;bottom:0;height:68px;background:var(--dark)}
.cta{position:absolute;left:0;height:40px;width:236px;background:var(--red);color:var(--white);font-family:"Oswald",Arial,sans-serif;font-weight:500;font-size:19px;display:flex;align-items:center;padding-left:26px;border-radius:0 20px 20px 0;letter-spacing:.3px}
.contact{position:absolute;bottom:16px;display:flex;align-items:center;gap:6px;color:var(--white);font-size:14px;font-weight:500;white-space:nowrap}
.contact .ic{width:16px;height:16px;border-radius:50%;background:var(--blue);display:flex;align-items:center;justify-content:center}
</style>
</head>
<body>

<!-- Side one: air source heat pumps -->
<section class="flyer flyer--heat">
  <div class="photo photo--family" role="img" aria-label="Photo of a family relaxing on a sofa at home beside an outdoor heat pump unit and indoor cylinder"></div>
  <svg class="abs" style="left:0;top:120px" width="560" height="110" viewBox="0 0 560 110" aria-hidden="true">
    <path d="M0 50 C200 75 420 55 560 0 L560 0 L0 0Z" fill="#fff"/>
    <path d="M0 50 C200 75 420 55 560 0 L560 20 C420 80 200 100 0 78Z" fill="var(--blue)"/>
    <path d="M0 78 C200 100 420 80 560 20 L560 28 C420 90 200 110 0 86Z" fill="#fff" opacity=".9"/>
  </svg>
  <svg class="abs" style="left:0;top:362px" width="560" height="70" viewBox="0 0 560 70" aria-hidden="true">
    <path d="M0 40 C160 10 380 0 560 30 L560 70 L0 70Z" fill="var(--red)"/>
    <path d="M0 52 C160 22 380 14 560 44 L560 70 L0 70Z" fill="#fff"/>
  </svg>

  <div class="brand" style="left:22px;top:46px">Harlow</div>
  <div class="tagline" style="left:26px;top:108px">Climawell services for business.</div>

  <div class="phone-pill" style="right:22px;top:22px">
    <span class="dot"><svg width="14" height="14" viewBox="0 0 24 24"><path fill="#fff" d="M6.6 10.8a15 15 0 0 0 6.6 6.6l2.2-2.2a1 1 0 0 1 1-.25 11.4 11.4 0 0 0 3.6.57 1 1 0 0 1 1 1V20a1 1 0 0 1-1 1A17 17 0 0 1 3 4a1 1 0 0 1 1-1h3.5a1 1 0 0 1 1 1c0 1.25.2 2.45.57 3.6a1 1 0 0 1-.25 1z"/></svg></span>0800 555 0192
  </div>
  <div class="pill-note" style="right:24px;top:62px">Our experts will help you find the right air<br>source heat pump at the right price for you.</div>

  <h2 class="heading" style="left:22px;top:440px">Air Source Heat Pumps</h2>
  <div class="rule" style="left:22px;top:478px;width:250px"></div>
  <div class="subhead" style="left:22px;top:486px">Air to water Heat pump<br>Instalation + maintenance</div>
  <div class="body-copy" style="left:22px;top:536px;width:256px">
    <p>Air Source Heat Pumps (ASHP) are the new green alternative to your oil or gas boiler for your homes heating and hot water requirements that will help build towards a cleaner environment for future generations.</p>
    <p>Our installations are all MCS accredited which allows access to the financial incentives. All of our air source heat pump installations are protected under warranty for your peace of mind.</p>
  </div>

  <div class="vline" style="left:290px;top:440px;height:230px"></div>
  <ul class="benefits benefits--heat" style="left:302px;top:440px;width:250px">
    <li><svg width="24" height="24" viewBox="0 0 24 24"><rect x="4" y="3" width="14" height="18" rx="2" fill="none" stroke="var(--red)" stroke-width="1.6"/><path d="M7 8h8M7 12h8M7 16h5" stroke="var(--blue)" stroke-width="1.6"/></svg>Reduce your energy bills</li>
    <li><svg width="24" height="24" viewBox="0 0 24 24"><path d="M6 20V9l6-4v15M12 20h7V11l-4-2" fill="none" stroke="var(--red)" stroke-width="1.6"/><circle cx="18" cy="6" r="3" fill="var(--blue)"/></svg>Safeguard against rising fuel prices</li>
    <li><svg width="24" height="24" viewBox="0 0 24 24"><circle cx="12" cy="10" r="5" fill="none" stroke="var(--red)" stroke-width="1.6"/><path d="M10 17h4M10 20h4" stroke="var(--blue)" stroke-width="1.6"/></svg>No chimneys or flues producing<br>harmful emissions</li>
    <li><svg width="24" height="24" viewBox="0 0 24 24"><path d="M3 12l9-8 9 8M6 10v10h12V10" fill="none" stroke="var(--red)" stroke-width="1.6"/><rect x="10" y="14" width="4" height="6" fill="var(--blue)"/></svg>Raise your property value</li>
    <li><svg width="24" height="24" viewBox="0 0 24 24"><path d="M4 20V14M9 20V10M14 20V12M19 20V6" stroke="var(--red)" stroke-width="2"/><path d="M4 10l5-4 5 3 5-6" fill="none" stroke="var(--blue)" stroke-width="1.6"/></svg>Reduce your home's carbon<br>footprint</li>
    <li><svg width="24" height="24" viewBox="0 0 24 24"><path d="M3 12l9-8 9 8M6 10v10h12V10" fill="none" stroke="var(--red)" stroke-width="1.6"/><path d="M13 11l-3 4h3l-2 4" fill="none" stroke="var(--blue)" stroke-width="1.6"/></svg>Power your home with 100%<br>renewable energy</li>
    <li><svg width="24" height="24" viewBox="0 0 24 24"><circle cx="13" cy="9" r="5" fill="none" stroke="var(--blue)" stroke-width="1.6"/><path d="M3 19l5-3h6l5-2" fill="none" stroke="var(--red)" stroke-width="1.6"/></svg>Receive as much as £13,900 in payment<br>from the Renewable Heat Incentive</li>
  </ul>

  <div class="footer">
    <div class="contact" style="left:22px"><span class="ic"><svg width="9" height="9" viewBox="0 0 10 10"><rect x="1" y="2" width="8" height="6" fill="none" stroke="#fff" stroke-width="1"/><path d="M1 2l4 3 4-3" fill="none" stroke="#fff" stroke-width="1"/></svg></span>info@harlowclimawell.co.uk</div>
    <div class="contact" style="left:252px"><span class="ic"><svg width="9" height="9" viewBox="0 0 24 24"><path fill="#fff" d="M6.6 10.8a15 15 0 0 0 6.6 6.6l2.2-2.2a1 1 0 0 1 1-.25 11 11 0 0 0 3.6.57 1 1 0 0 1 1 1V20a1 1 0 0 1-1 1A17 17 0 0 1 3 4a1 1 0 0 1 1-1h3.5a1 1 0 0 1 1 1c0 1.25.2 2.45.57 3.6a1 1 0 0 1-.25 1z"/></svg></span>0800 555 0192</div>
    <div class="contact" style="left:380px;font-size:12.5px"><span class="ic"><svg width="10" height="10" viewBox="0 0 10 10"><circle cx="5" cy="5" r="4" fill="none" stroke="#fff"/><path d="M1 5h8M5 1c2 2 2 6 0 8M5 1c-2 2-2 6 0 8" fill="none" stroke="#fff" stroke-width=".8"/></svg></span>www.harlowclimawell.co.uk</div>
  </div>
  <div class="cta" style="bottom:50px">CONTACT US TODAY</div>
</section>

<!-- Side two: air conditioning heat pumps -->
<section class="flyer flyer--air">
  <div class="photo photo--garden" role="img" aria-label="Photo of an outdoor heat pump unit beside a white house with a garden and terrace"></div>
  <svg class="abs" style="left:0;top:230px" width="560" height="120" viewBox="0 0 560 120" aria-hidden="true">
    <path d="M0 110 C180 60 380 40 560 50 L560 120 L0 120Z" fill="#fff"/>
    <path d="M0 100 C180 48 380 28 560 38 L560 50 C380 40 180 60 0 110Z" fill="var(--blue)"/>
  </svg>
  <div class="inset" style="left:300px;top:200px" role="img" aria-label="Close-up photo of an indoor air conditioning unit and remote"></div>
  <div class="inset" style="left:425px;top:190px" role="img" aria-label="Close-up photo of a wall-mounted air conditioning unit"></div>

  <div class="brand" style="left:24px;top:334px">Harlow</div>
  <div class="tagline" style="left:28px;top:396px">Climawell services for business.</div>
  <h2 class="heading" style="left:24px;top:420px;font-size:20px">Air Conditioning Heat Pumps</h2>
  <div class="rule" style="left:24px;top:450px;width:250px"></div>
  <div class="subhead" style="left:24px;top:456px;font-size:16px">Air to Air Heat Pumps<br>Air Conditioning Heat Pumps<br>Installation + maintenance</div>
  <div class="body-copy" style="left:24px;top:516px;width:256px;font-size:10px;line-height:1.38">
    <p>Enhance the comfort of your home with an Air Conditioning heat pump. We supply and fit latest energy-efficient systems to keep your living space at the right temperature all year round and help reduce your heating bills.</p>
    <p>Modern Air Conditioning heat pumps are one of the most efficient forms of heating available over conventional methods like gas and electric heating. We have had reports of customers using 1/5 of the energy after we have installed a system, resulting in massive savings off these customers' heating bills.</p>
  </div>

  <div class="vline" style="left:290px;top:330px;height:270px"></div>
  <ul class="benefits benefits--air" style="left:302px;top:326px;width:250px">
    <li><svg width="26" height="26" viewBox="0 0 26 26"><circle cx="13" cy="13" r="11" fill="var(--blue)" stroke="var(--red)" stroke-width="1.5"/><path d="M13 6v14M7 9.5l12 7M7 16.5l12-7" stroke="#fff" stroke-width="1.4"/></svg>Cools in summer</li>
    <li><svg width="26" height="26" viewBox="0 0 26 26"><circle cx="13" cy="13" r="11" fill="var(--blue)" stroke="var(--red)" stroke-width="1.5"/><rect x="11" y="6" width="4" height="10" rx="2" fill="none" stroke="#fff" stroke-width="1.3"/><circle cx="13" cy="18" r="2.5" fill="#fff"/></svg>Efficiently heats in winter</li>
    <li><svg width="26" height="26" viewBox="0 0 26 26"><circle cx="13" cy="13" r="11" fill="var(--blue)" stroke="var(--red)" stroke-width="1.5"/><path d="M8 18v-4M11 18v-7M14 18v-5M17 18V9" stroke="#fff" stroke-width="1.6"/></svg>Reduce heating bills</li>
    <li><svg width="26" height="26" viewBox="0 0 26 26"><circle cx="13" cy="13" r="11" fill="var(--blue)" stroke="var(--red)" stroke-width="1.5"/><path d="M7 10h9a2 2 0 1 0-2-2M7 14h11a2 2 0 1 1-2 2" fill="none" stroke="#fff" stroke-width="1.4"/></svg>Purifies the air</li>
    <li><svg width="26" height="26" viewBox="0 0 26 26"><circle cx="13" cy="13" r="11" fill="var(--blue)" stroke="var(--red)" stroke-width="1.5"/><path d="M13 6c-3 4-4 6-4 8a4 4 0 0 0 8 0c0-2-1-4-4-8z" fill="none" stroke="#fff" stroke-width="1.3"/><path d="M8 18l10-10" stroke="#fff" stroke-width="1.3"/></svg>Dehumidifier</li>
    <li><svg width="26" height="26" viewBox="0 0 26 26"><circle cx="13" cy="13" r="11" fill="var(--blue)" stroke="var(--red)" stroke-width="1.5"/><circle cx="13" cy="12" r="4.5" fill="none" stroke="#fff" stroke-width="1.3"/><path d="M11 19h4" stroke="#fff" stroke-width="1.3"/></svg>Energy efficient systems</li>
  </ul>
  <div class="price" style="left:306px;top:524px">Energy-efficient air conditioning<br>systems from only £1,550</div>

  <div class="phone-pill" style="left:304px;top:566px">
    <span class="dot"><svg width="14" height="14" viewBox="0 0 24 24"><path fill="#fff" d="M6.6 10.8a15 15 0 0 0 6.6 6.6l2.2-2.2a1 1 0 0 1 1-.25 11.4 11.4 0 0 0 3.6.57 1 1 0 0 1 1 1V20a1 1 0 0 1-1 1A17 17 0 0 1 3 4a1 1 0 0 1 1-1h3.5a1 1 0 0 1 1 1c0 1.25.2 2.45.57 3.6a1 1 0 0 1-.25 1z"/></svg></span>0800 555 0192
  </div>
  <div class="pill-note" style="right:22px;top:606px">Our experts will help you find the right air<br>source heat pump at the right price for you.</div>

  <div class="footer">
    <div class="contact" style="left:22px"><span class="ic"><svg width="9" height="9" viewBox="0 0 10 10"><rect x="1" y="2" width="8" height="6" fill="none" stroke="#fff" stroke-width="1"/><path d="M1 2l4 3 4-3" fill="none" stroke="#fff" stroke-width="1"/></svg></span>info@harlowclimawell.co.uk</div>
    <div class="contact" style="left:252px"><span class="ic"><svg width="9" height="9" viewBox="0 0 24 24"><path fill="#fff" d="M6.6 10.8a15 15 0 0 0 6.6 6.6l2.2-2.2a1 1 0 0 1 1-.25 11 11 0 0 0 3.6.57 1 1 0 0 1 1 1V20a1 1 0 0 1-1 1A17 17 0 0 1 3 4a1 1 0 0 1 1-1h3.5a1 1 0 0 1 1 1c0 1.25.2 2.45.57 3.6a1 1 0 0 1-.25 1z"/></svg></span>0800 555 0192</div>
    <div class="contact" style="left:380px;font-size:12.5px"><span class="ic"><svg width="10" height="10" viewBox="0 0 10 10"><circle cx="5" cy="5" r="4" fill="none" stroke="#fff"/><path d="M1 5h8M5 1c2 2 2 6 0 8M5 1c-2 2-2 6 0 8" fill="none" stroke="#fff" stroke-width=".8"/></svg></span>www.harlowclimawell.co.uk</div>
  </div>
  <div class="cta" style="bottom:50px">CONTACT US TODAY</div>
</section>

</body>
</html>
```